Tidewell Comforts, a portable luxury restroom trailer company needs a landing page

We need a landing page for a luxury portable restroom trailer company. This should be modern, and simple - use any combination of Pantone colors: Warm Gray 1C, Black 7C, 7529c, 873C, 8003C

We rent these trailers for special events like weddings, private parties, festivals, family reunions, team building, wine tastings, beer tastings, food truck round-ups, etc.

An idea of the landing page is in the files below. Please use stock photography and placeholder text for now. The winning design will be given final content.

Requirements
Must have
• Multiple "Get Quote" buttons or a place for them to type in type of rental, how many people etc

```html
<!DOCTYPE html>
<html lang="en">
<head>
<meta charset="utf-8">
<title>Tidewell Comforts – Landing Page Concepts</title>
<link href="https://fonts.googleapis.com/css2?family=Oswald:wght@500;600&family=Roboto:wght@400;500&display=swap" rel="stylesheet">
<style>
:root{
  --stage:#2d2d2d;
  --blue:#1766b0;
  --blue-deep:#0e4f8f;
  --blue-soft:#3f8ccc;
  --ink:#222831;
  --muted:#5b6168;
  --line:#e3e6ea;
  --footer:#1b2532;
  --footer-line:#2d3a4a;
  --white:#ffffff;
  --field:#f1f3f5;
  --tyre:#2b2d30;
}
*{box-sizing:border-box;margin:0;padding:0}
html,body{width:1200px;height:1002px;overflow:hidden;background:var(--stage)}
.board{position:absolute;left:0;top:0;width:2100px;height:1753px;transform:scale(.5714286);transform-origin:0 0;background:var(--stage);font-family:"Roboto",sans-serif;color:var(--ink)}
.page{position:absolute;top:45px;width:637px;height:1674px;background:var(--white);overflow:hidden}
.page--collage{left:66px}.page--trailer{left:743px}.page--modal{left:1419px}
.h{font-family:"Oswald",sans-serif;font-weight:600;text-transform:uppercase;letter-spacing:.2px}

/* header */
.site-header{position:absolute;left:0;top:0;width:637px;height:42px;background:var(--white)}
.brand{position:absolute;left:70px;top:6px;display:flex;align-items:center;gap:5px}
.brand-mark{width:28px;height:28px;border:2px solid var(--blue);border-radius:4px}
.brand-name{font-family:"Oswald",sans-serif;font-weight:600;font-size:10px;line-height:11px;color:var(--ink);text-transform:uppercase}
.nav{position:absolute;left:304px;top:15px;display:flex;gap:14px;font-size:7px;font-weight:500;color:var(--ink)}
.phone-pill{position:absolute;left:474px;top:9px;width:92px;height:22px;border-radius:11px;background:var(--blue);color:var(--white);font-family:"Oswald",sans-serif;font-size:8.5px;display:flex;align-items:center;padding-left:3px;gap:7px}
.phone-pill i{width:16px;height:16px;border-radius:50%;background:var(--white);display:flex;align-items:center;justify-content:center}

/* hero variants */
.hero-collage{position:absolute;left:0;top:42px;width:637px;height:315px;background:var(--blue)}
.collage{position:absolute;left:10px;top:33px;width:615px;height:250px;background:linear-gradient(90deg,#2f5f98,#3f80c4 50%,#2f5f98)}
.hero-collage .title{position:absolute;left:0;width:637px;top:110px;text-align:center;color:var(--white);font-size:28px;line-height:36px}
.hero-trailer{position:absolute;left:0;top:42px;width:637px;height:318px;border-radius:60px 60px 45px 45px;background:linear-gradient(100deg,#5d9fd6,#2c78bd 45%,#3d84c4 70%,#1d62a5)}
.hero-trailer .title{position:absolute;left:0;width:637px;top:72px;text-align:center;color:var(--white);font-size:35px;line-height:37px}
.hero-trailer .lede{position:absolute;left:110px;width:417px;top:152px;text-align:center;color:#e8f1fa;font-size:6.5px;line-height:13px}
.btn-quote{position:absolute;left:272px;top:190px;width:92px;height:22px;border-radius:11px;background:var(--white);color:var(--blue);font-family:"Oswald",sans-serif;font-weight:500;font-size:8px;display:flex;align-items:center;justify-content:center}
.wheel{position:absolute;width:150px;height:150px;border-radius:50%;background:var(--white);padding:9px}
.wheel span{display:block;width:100%;height:100%;border-radius:50%;background:var(--tyre)}

/* sections */
.sec-title{position:absolute;left:0;width:637px;text-align:center;font-size:18px;line-height:23px;color:var(--ink)}
.rule{position:absolute;left:305px;width:27px;height:2px;background:var(--blue)}
.arrow{position:absolute;top:576px;width:12px;height:16px}
.card{position:absolute;top:517px;width:160px;height:214px;background:var(--white);box-shadow:0 1px 6px rgba(0,0,0,.15);text-align:center}
.card .ph{position:absolute;left:3px;top:3px;width:154px;height:100px}
.card .ct{position:absolute;left:0;width:160px;top:110px;font-size:8.5px}
.card p{position:absolute;left:8px;width:144px;top:126px;font-size:6.2px;line-height:12.8px;color:var(--muted)}
.btn-line{position:absolute;height:19px;border:1.3px solid var(--blue);border-radius:10px;color:var(--blue);font-family:"Oswald",sans-serif;font-weight:500;font-size:6.5px;display:flex;align-items:center;justify-content:center}
.card .btn-line{left:48px;width:66px;top:183px}
.about{position:absolute;left:0;top:775px;width:637px;height:229px;border-radius:56px;background:linear-gradient(180deg,#2a73b7,#1d65aa 60%,#2c6fa8)}
.about .h{position:absolute;left:0;width:637px;top:33px;text-align:center;color:var(--white);font-size:18px}
.about .rule{background:var(--white);top:64px}
.about p{position:absolute;left:88px;width:461px;top:73px;text-align:center;color:#eaf2fa;font-size:6.4px;line-height:12.8px}
.product{position:absolute;width:162px;height:191px;border:1px solid var(--line);background:var(--white);text-align:center}
.product .ph{position:absolute;left:0;top:0;width:160px;height:107px}
.product .pt{position:absolute;left:0;width:160px;top:114px;font-size:8px}
.product p{position:absolute;left:10px;width:140px;top:131px;font-size:6.2px;line-height:12.8px;color:var(--muted)}
.product .btn-line{left:47px;width:68px;top:160px}

/* footer */
.site-footer{position:absolute;left:0;top:1514px;width:637px;height:160px;background:var(--footer);color:#d8dee6;font-size:6.8px}
.contact-row{position:absolute;top:35px;left:0;width:637px;display:flex;justify-content:center;gap:46px}
.contact-row span{display:flex;align-items:center;gap:5px}
.foot-nav{position:absolute;top:65px;left:0;width:637px;display:flex;justify-content:center;gap:14px;font-weight:500;color:var(--white)}
.foot-rule{position:absolute;top:93px;left:0;width:637px;height:1px;background:var(--footer-line)}
.socials{position:absolute;top:107px;left:0;width:637px;display:flex;justify-content:center;gap:8px}
.socials i{width:16px;height:16px;border-radius:50%;border:1px solid #cfd6de}
.copy{position:absolute;top:135px;left:0;width:637px;text-align:center;color:var(--white);font-weight:500;font-size:6.5px}

/* dimmed quote state */
.dim{position:absolute;inset:0;background:rgba(0,0,0,.55)}
.quote-modal{position:absolute;left:54px;top:269px;width:520px;height:308px;border-radius:40px;background:var(--white)}
.quote-modal .h{position:absolute;left:0;width:520px;top:20px;text-align:center;font-size:13px;color:var(--ink)}
.field{position:absolute;height:23px;border:1px solid var(--line);background:var(--white);display:flex;align-items:center;font-size:6px;color:var(--ink)}
.field b{width:22px;height:21px;background:var(--field);margin-right:9px;display:flex;align-items:center;justify-content:center}
.field b i{width:7px;height:7px;border-radius:2px;background:var(--blue)}
.field em{position:absolute;right:7px;top:8px;border:3px solid transparent;border-top:4px solid var(--ink)}
.f-l{left:100px;width:162px}.f-r{left:268px;width:161px}.f-w{left:100px;width:329px}
.btn-submit{position:absolute;left:230px;top:250px;width:66px;height:20px;border-radius:10px;background:var(--blue);color:var(--white);font-family:"Oswald",sans-serif;font-weight:500;font-size:7px;display:flex;align-items:center;justify-content:center}
</style>
</head>
<body>
<div class="board">

<!-- ===== Concept A: collage hero ===== -->
<section class="page page--collage">
  <header class="site-header">
    <div class="brand"><span class="brand-mark"></span><span class="brand-name">Tidewell<br>Comforts</span></div>
    <nav class="nav"><span>HOME</span><span>EVENTS</span><span>PRODUCTS</span><span>CONTACT</span></nav>
    <div class="phone-pill"><i><svg width="8" height="8" viewBox="0 0 24 24"><path fill="#1766b0" d="M6.6 10.8a15 15 0 006.6 6.6l2.2-2.2a1 1 0 011-.25 11.4 11.4 0 003.6.57 1 1 0 011 1V20a1 1 0 01-1 1A17 17 0 013 4a1 1 0 011-1h3.5a1 1 0 011 1c0 1.25.2 2.45.57 3.57a1 1 0 01-.25 1z"/></svg></i>+1 555 0142 736</div>
  </header>
  <div class="hero-collage">
    <div class="collage" role="img" aria-label="Collage of event photos: weddings, parties, festivals and restroom trailers"></div>
    <div class="title h">Welcome to<br>Tidewell<br>Comforts</div>
  </div>

  <div class="sec-title h" style="top:445px">We rent these trailers for<br>special events</div>
  <div class="rule" style="top:496px"></div>
  <svg class="arrow" style="left:42px" viewBox="0 0 12 16"><path d="M9 1L2 8l7 7" fill="none" stroke="#222" stroke-width="1.6"/></svg>
  <svg class="arrow" style="left:584px" viewBox="0 0 12 16"><path d="M3 1l7 7-7 7" fill="none" stroke="#222" stroke-width="1.6"/></svg>
  <article class="card" style="left:69px"><div class="ph" role="img" aria-label="Wooden restroom trailer with garden steps" style="background:linear-gradient(135deg,#7d9a5a,#c49a62)"></div><div class="ct h">Weddings</div><p>Lorem ipsum dolor sit amet, consectetur adip iscing elit, sed do eiusmod tempor incididunt ut labore et dolore magna aliqua Ut enim ad minim veniam quis nostrud.</p><div class="btn-line">LEARN MORE</div></article>
  <article class="card" style="left:239px"><div class="ph" role="img" aria-label="Trailer interior with sink and toilet" style="background:linear-gradient(135deg,#d9d4cc,#9a6a45)"></div><div class="ct h">Private Parties</div><p>Lorem ipsum dolor sit amet, consectetur adip iscing elit, sed do eiusmod tempor incididunt ut labore et dolore magna aliqua Ut enim ad minim veniam quis nostrud.</p><div class="btn-line">LEARN MORE</div></article>
  <article class="card" style="left:408px"><div class="ph" role="img" aria-label="Restroom stalls with lighting" style="background:linear-gradient(135deg,#2a2a35,#d8d0c4)"></div><div class="ct h">Festivals</div><p>Lorem ipsum dolor sit amet, consectetur adip iscing elit, sed do eiusmod tempor incididunt ut labore et dolore magna aliqua Ut enim ad minim veniam quis nostrud.</p><div class="btn-line">LEARN MORE</div></article>

  <div class="about" role="img" aria-label="Blue-tinted photo of a truck towing a trailer">
    <div class="h">About Tidewell Comforts</div><div class="rule"></div>
    <p>Lorem ipsum dolor sit amet, consectetur adipiscing elit, sed do eiusmod tempor incididunt ut labore et dolore magna aliqua. Ut enim ad minim veniam, quis nostrud exercitation ullamco laboris nisi ut aliquip ex ea commodo consequat. Duis aute irure dolor in reprehenderit in voluptate velit esse cillum dolore eu fugiat nulla pariatur. Excepteur sint occaecat cupidatat non proident, sunt in culpa qui officia deserunt mollit anim id est laborum Sed ut perspiciatis unde omnis iste natus error sit voluptatem accusantium doloremque laudantium, totam rem aperiam, eaque ipsa quae ab illo inventore veritatis et quasi architecto beatae vitae dicta sunt explicabo. Nemo enim ipsam voluptatem quia voluptas sit aspernatur aut odit aut fugit, sed quia consequuntur magni dolores eos qui ratione voluptatem sequi nesciunt. Neque porro quisquam est, qui dolorem ipsum quia dolor sit amet, consectetur, adipisci velit, sed quia non numquam eius modi tempora incidunt ut labore et dolore magnam aliquam quaerat voluptatem. Ut enim ad minima veniam, quis nostrum exercitationem ullam corporis suscipit laboriosam, nisi ut aliquid ex ea commodi consequatur.</p>
  </div>

  <div class="sec-title h" style="top:1043px">Our Product</div>
  <div class="rule" style="top:1070px"></div>
  <article class="product" style="left:69px;top:1086px"><div class="ph" role="img" aria-label="White two-station restroom trailer" style="background:linear-gradient(#e6e8ea,#c9cdd1)"></div><div class="pt h">2 Station Luxury Restroom Trailer</div><p>Lorem ipsum dolor sit amet, consectetur adip iscing elit, sed do eiusmod tempor.</p><div class="btn-line">ADD FOR QUOTE</div></article>
  <article class="product" style="left:238px;top:1086px"><div class="ph" role="img" aria-label="Restroom trailer at a construction site" style="background:linear-gradient(#8fb6dc,#a8794e)"></div><div class="pt h">5 Station Luxury Restroom Trailer</div><p>Lorem ipsum dolor sit amet, consectetur adip iscing elit, sed do eiusmod tempor.</p><div class="btn-line">ADD FOR QUOTE</div></article>
  <article class="product" style="left:406px;top:1086px"><div class="ph" role="img" aria-label="Large restroom trailer with people outside" style="background:linear-gradient(135deg,#b9b4aa,#5a5048)"></div><div class="pt h">9 Station Luxury Restroom Trailer</div><p>Lorem ipsum dolor sit amet, consectetur adip iscing elit, sed do eiusmod tempor.</p><div class="btn-line">ADD FOR QUOTE</div></article>
  <article class="product" style="left:69px;top:1283px"><div class="ph" role="img" aria-label="Colourful cleaning supplies" style="background:linear-gradient(135deg,#7a8590,#d85a3a 50%,#4a6ad0)"></div><div class="pt h">Grand Specialty Amenities Package</div><p>Lorem ipsum dolor sit amet, consectetur adip iscing elit, sed do eiusmod tempor.</p><div class="btn-line">ADD FOR QUOTE</div></article>
  <article class="product" style="left:238px;top:1283px"><div class="ph" role="img" aria-label="Hand under a sanitizer dispenser" style="background:linear-gradient(135deg,#e8e6e2,#b98a6c)"></div><div class="pt h">Hand Sanitizer Station Rentals</div><p>Lorem ipsum dolor sit amet, consectetur adip iscing elit, sed do eiusmod tempor.</p><div class="btn-line">ADD FOR QUOTE</div></article>
  <article class="product" style="left:406px;top:1283px"><div class="ph" role="img" aria-label="Restroom attendant cleaning a washroom" style="background:linear-gradient(135deg,#3a4250,#e4e7ea)"></div><div class="pt h">Restroom Attendant</div><p>Lorem ipsum dolor sit amet, consectetur adip iscing elit, sed do eiusmod tempor.</p><div class="btn-line">ADD FOR QUOTE</div></article>

  <footer class="site-footer">
    <div class="contact-row"><span><svg width="6" height="8" viewBox="0 0 12 16"><path fill="#fff" d="M6 0a6 6 0 00-6 6c0 4.5 6 10 6 10s6-5.5 6-10a6 6 0 00-6-6zm0 8.5A2.5 2.5 0 116 3.5a2.5 2.5 0 010 5z"/></svg>123 Lorem ipsum dolor sit amet consectetur</span><span><svg width="7" height="7" viewBox="0 0 24 24"><path fill="#fff" d="M6.6 10.8a15 15 0 006.6 6.6l2.2-2.2a1 1 0 011-.25 11.4 11.4 0 003.6.57 1 1 0 011 1V20a1 1 0 01-1 1A17 17 0 013 4a1 1 0 011-1h3.5a1 1 0 011 1c0 1.25.2 2.45.57 3.57a1 1 0 01-.25 1z"/></svg>+1 555 0142 736</span><span><svg width="8" height="6" viewBox="0 0 16 12"><rect width="16" height="12" rx="1" fill="#fff"/><path d="M1 1l7 5 7-5" fill="none" stroke="#1b2532" stroke-width="1.4"/></svg>hello@tidewellcomforts.com</span></div>
    <div class="foot-nav"><span>HOME</span><span>|</span><span>EVENTS</span><span>|</span><span>PRODUCTS</span><span>|</span><span>CONTACT</span></div>
    <div class="foot-rule"></div>
    <div class="socials"><i></i><i></i><i></i><i></i></div>
    <div class="copy">© Copyrights 2022 Tidewell Comforts &nbsp;|&nbsp; All Rights Reserved</div>
  </footer>
</section>

<!-- ===== Concept B: trailer hero ===== -->
<section class="page page--trailer">
  <header class="site-header">
    <div class="brand"><span class="brand-mark"></span><span class="brand-name">Tidewell<br>Comforts</span></div>
    <nav class="nav"><span>HOME</span><span>EVENTS</span><span>PRODUCTS</span><span>CONTACT</span></nav>
    <div class="phone-pill"><i><svg width="8" height="8" viewBox="0 0 24 24"><path fill="#1766b0" d="M6.6 10.8a15 15 0 006.6 6.6l2.2-2.2a1 1 0 011-.25 11.4 11.4 0 003.6.57 1 1 0 011 1V20a1 1 0 01-1 1A17 17 0 013 4a1 1 0 011-1h3.5a1 1 0 011 1c0 1.25.2 2.45.57 3.57a1 1 0 01-.25 1z"/></svg></i>+1 555 0142 736</div>
  </header>
  <div class="hero-trailer" role="img" aria-label="Blue-tinted photo of a restroom trailer with workers">
    <div class="title h">Welcome to<br>Tidewell Comforts</div>
    <p class="lede">Lorem ipsum dolor sit amet, consectetur adipiscing elit, sed do eiusmod tempor incididunt ut labore et dolore magna aliqua. Ut enim ad minim veniam, quis nostrud exercitation ullamco laboris nisi ut aliquip ex ea commodo consequat.</p>
    <div class="btn-quote">REQUEST A QUOTE</div>
  </div>
  <div class="wheel" style="left:62px;top:285px" role="img" aria-label="Photo of a trailer tyre"><span></span></div>
  <div class="wheel" style="left:422px;top:285px" role="img" aria-label="Photo of a trailer tyre"><span></span></div>

  <div class="sec-title h" style="top:445px">We rent these trailers for<br>special events</div>
  <div class="rule" style="top:496px"></div>
  <svg class="arrow" style="left:42px" viewBox="0 0 12 16"><path d="M9 1L2 8l7 7" fill="none" stroke="#222" stroke-width="1.6"/></svg>
  <svg class="arrow" style="left:584px" viewBox="0 0 12 16"><path d="M3 1l7 7-7 7" fill="none" stroke="#222" stroke-width="1.6"/></svg>
  <article class="card" style="left:69px"><div class="ph" role="img" aria-label="Wooden restroom trailer with garden steps" style="background:linear-gradient(135deg,#7d9a5a,#c49a62)"></div><div class="ct h">Weddings</div><p>Lorem ipsum dolor sit amet, consectetur adip iscing elit, sed do eiusmod tempor incididunt ut labore et dolore magna aliqua Ut enim ad minim veniam quis nostrud.</p><div class="btn-line">LEARN MORE</div></article>
  <article class="card" style="left:239px"><div class="ph" role="img" aria-label="Trailer interior with sink and toilet" style="background:linear-gradient(135deg,#d9d4cc,#9a6a45)"></div><div class="ct h">Private Parties</div><p>Lorem ipsum dolor sit amet, consectetur adip iscing elit, sed do eiusmod tempor incididunt ut labore et dolore magna aliqua Ut enim ad minim veniam quis nostrud.</p><div class="btn-line">LEARN MORE</div></article>
  <article class="card" style="left:408px"><div class="ph" role="img" aria-label="Restroom stalls with lighting" style="background:linear-gradient(135deg,#2a2a35,#d8d0c4)"></div><div class="ct h">Festivals</div><p>Lorem ipsum dolor sit amet, consectetur adip iscing elit, sed do eiusmod tempor incididunt ut labore et dolore magna aliqua Ut enim ad minim veniam quis nostrud.</p><div class="btn-line">LEARN MORE</div></article>

  <div class="about" role="img" aria-label="Blue-tinted photo of a truck towing a trailer">
    <div class="h">About Tidewell Comforts</div><div class="rule"></div>
    <p>Lorem ipsum dolor sit amet, consectetur adipiscing elit, sed do eiusmod tempor incididunt ut labore et dolore magna aliqua. Ut enim ad minim veniam, quis nostrud exercitation ullamco laboris nisi ut aliquip ex ea commodo consequat. Duis aute irure dolor in reprehenderit in voluptate velit esse cillum dolore eu fugiat nulla pariatur. Excepteur sint occaecat cupidatat non proident, sunt in culpa qui officia deserunt mollit anim id est laborum Sed ut perspiciatis unde omnis iste natus error sit voluptatem accusantium doloremque laudantium, totam rem aperiam, eaque ipsa quae ab illo inventore veritatis et quasi architecto beatae vitae dicta sunt explicabo. Nemo enim ipsam voluptatem quia voluptas sit aspernatur aut odit aut fugit, sed quia consequuntur magni dolores eos qui ratione voluptatem sequi nesciunt. Neque porro quisquam est, qui dolorem ipsum quia dolor sit amet, consectetur, adipisci velit, sed quia non numquam eius modi tempora incidunt ut labore et dolore magnam aliquam quaerat voluptatem. Ut enim ad minima veniam, quis nostrum exercitationem ullam corporis suscipit laboriosam, nisi ut aliquid ex ea commodi consequatur.</p>
  </div>

  <div class="sec-title h" style="top:1043px">Our Product</div>
  <div class="rule" style="top:1070px"></div>
  <article class="product" style="left:69px;top:1086px"><div class="ph" role="img" aria-label="White two-station restroom trailer" style="background:linear-gradient(#e6e8ea,#c9cdd1)"></div><div class="pt h">2 Station Luxury Restroom Trailer</div><p>Lorem ipsum dolor sit amet, consectetur adip iscing elit, sed do eiusmod tempor.</p><div class="btn-line">ADD FOR QUOTE</div></article>
  <article class="product" style="left:238px;top:1086px"><div class="ph" role="img" aria-label="Restroom trailer at a construction site" style="background:linear-gradient(#8fb6dc,#a8794e)"></div><div class="pt h">5 Station Luxury Restroom Trailer</div><p>Lorem ipsum dolor sit amet, consectetur adip iscing elit, sed do eiusmod tempor.</p><div class="btn-line">ADD FOR QUOTE</div></article>
  <article class="product" style="left:406px;top:1086px"><div class="ph" role="img" aria-label="Large restroom trailer with people outside" style="background:linear-gradient(135deg,#b9b4aa,#5a5048)"></div><div class="pt h">9 Station Luxury Restroom Trailer</div><p>Lorem ipsum dolor sit amet, consectetur adip iscing elit, sed do eiusmod tempor.</p><div class="btn-line">ADD FOR QUOTE</div></article>
  <article class="product" style="left:69px;top:1283px"><div class="ph" role="img" aria-label="Colourful cleaning supplies" style="background:linear-gradient(135deg,#7a8590,#d85a3a 50%,#4a6ad0)"></div><div class="pt h">Grand Specialty Amenities Package</div><p>Lorem ipsum dolor sit amet, consectetur adip iscing elit, sed do eiusmod tempor.</p><div class="btn-line">ADD FOR QUOTE</div></article>
  <article class="product" style="left:238px;top:1283px"><div class="ph" role="img" aria-label="Hand under a sanitizer dispenser" style="background:linear-gradient(135deg,#e8e6e2,#b98a6c)"></div><div class="pt h">Hand Sanitizer Station Rentals</div><p>Lorem ipsum dolor sit amet, consectetur adip iscing elit, sed do eiusmod tempor.</p><div class="btn-line">ADD FOR QUOTE</div></article>
  <article class="product" style="left:406px;top:1283px"><div class="ph" role="img" aria-label="Restroom attendant cleaning a washroom" style="background:linear-gradient(135deg,#3a4250,#e4e7ea)"></div><div class="pt h">Restroom Attendant</div><p>Lorem ipsum dolor sit amet, consectetur adip iscing elit, sed do eiusmod tempor.</p><div class="btn-line">ADD FOR QUOTE</div></article>

  <footer class="site-footer">
    <div class="contact-row"><span><svg width="6" height="8" viewBox="0 0 12 16"><path fill="#fff" d="M6 0a6 6 0 00-6 6c0 4.5 6 10 6 10s6-5.5 6-10a6 6 0 00-6-6zm0 8.5A2.5 2.5 0 116 3.5a2.5 2.5 0 010 5z"/></svg>123 Lorem ipsum dolor sit amet consectetur</span><span><svg width="7" height="7" viewBox="0 0 24 24"><path fill="#fff" d="M6.6 10.8a15 15 0 006.6 6.6l2.2-2.2a1 1 0 011-.25 11.4 11.4 0 003.6.57 1 1 0 011 1V20a1 1 0 01-1 1A17 17 0 013 4a1 1 0 011-1h3.5a1 1 0 011 1c0 1.25.2 2.45.57 3.57a1 1 0 01-.25 1z"/></svg>+1 555 0142 736</span><span><svg width="8" height="6" viewBox="0 0 16 12"><rect width="16" height="12" rx="1" fill="#fff"/><path d="M1 1l7 5 7-5" fill="none" stroke="#1b2532" stroke-width="1.4"/></svg>hello@tidewellcomforts.com</span></div>
    <div class="foot-nav"><span>HOME</span><span>|</span><span>EVENTS</span><span>|</span><span>PRODUCTS</span><span>|</span><span>CONTACT</span></div>
    <div class="foot-rule"></div>
    <div class="socials"><i></i><i></i><i></i><i></i></div>
    <div class="copy">© Copyrights 2022 Tidewell Comforts &nbsp;|&nbsp; All Rights Reserved</div>
  </footer>
</section>

<!-- ===== Concept B: quote request open ===== -->
<section class="page page--modal">
  <header class="site-header">
    <div class="brand"><span class="brand-mark"></span><span class="brand-name">Tidewell<br>Comforts</span></div>
    <nav class="nav"><span>HOME</span><span>EVENTS</span><span>PRODUCTS</span><span>CONTACT</span></nav>
    <div class="phone-pill"><i><svg width="8" height="8" viewBox="0 0 24 24"><path fill="#1766b0" d="M6.6 10.8a15 15 0 006.6 6.6l2.2-2.2a1 1 0 011-.25 11.4 11.4 0 003.6.57 1 1 0 011 1V20a1 1 0 01-1 1A17 17 0 013 4a1 1 0 011-1h3.5a1 1 0 011 1c0 1.25.2 2.45.57 3.57a1 1 0 01-.25 1z"/></svg></i>+1 555 0142 736</div>
  </header>
  <div class="hero-trailer" role="img" aria-label="Blue-tinted photo of a restroom trailer with workers">
    <div class="title h">Welcome to<br>Tidewell Comforts</div>
    <p class="lede">Lorem ipsum dolor sit amet, consectetur adipiscing elit, sed do eiusmod tempor incididunt ut labore et dolore magna aliqua. Ut enim ad minim veniam, quis nostrud exercitation ullamco laboris nisi ut aliquip ex ea commodo consequat.</p>
    <div class="btn-quote">REQUEST A QUOTE</div>
  </div>

  <div class="sec-title h" style="top:445px">We rent these trailers for<br>special events</div>
  <svg class="arrow" style="left:42px" viewBox="0 0 12 16"><path d="M9 1L2 8l7 7" fill="none" stroke="#222" stroke-width="1.6"/></svg>
  <svg class="arrow" style="left:584px" viewBox="0 0 12 16"><path d="M3 1l7 7-7 7" fill="none" stroke="#222" stroke-width="1.6"/></svg>
  <article class="card" style="left:69px"><div class="ph" role="img" aria-label="Wooden restroom trailer with garden steps" style="background:linear-gradient(135deg,#7d9a5a,#c49a62)"></div><div class="ct h">Weddings</div><p>Lorem ipsum dolor sit amet, consectetur adip iscing elit, sed do eiusmod tempor incididunt ut labore et dolore magna aliqua Ut enim ad minim veniam quis nostrud.</p><div class="btn-line">LEARN MORE</div></article>
  <article class="card" style="left:239px"><div class="ph" role="img" aria-label="Trailer interior with sink and toilet" style="background:linear-gradient(135deg,#d9d4cc,#9a6a45)"></div><div class="ct h">Private Parties</div><p>Lorem ipsum dolor sit amet, consectetur adip iscing elit, sed do eiusmod tempor incididunt ut labore et dolore magna aliqua Ut enim ad minim veniam quis nostrud.</p><div class="btn-line">LEARN MORE</div></article>
  <article class="card" style="left:408px"><div class="ph" role="img" aria-label="Restroom stalls with lighting" style="background:linear-gradient(135deg,#2a2a35,#d8d0c4)"></div><div class="ct h">Festivals</div><p>Lorem ipsum dolor sit amet, consectetur adip iscing elit, sed do eiusmod tempor incididunt ut labore et dolore magna aliqua Ut enim ad minim veniam quis nostrud.</p><div class="btn-line">LEARN MORE</div></article>

  <div class="about" role="img" aria-label="Blue-tinted photo of a truck towing a trailer">
    <div class="h">About Tidewell Comforts</div><div class="rule"></div>
    <p>Lorem ipsum dolor sit amet, consectetur adipiscing elit, sed do eiusmod tempor incididunt ut labore et dolore magna aliqua. Ut enim ad minim veniam, quis nostrud exercitation ullamco laboris nisi ut aliquip ex ea commodo consequat. Duis aute irure dolor in reprehenderit in voluptate velit esse cillum dolore eu fugiat nulla pariatur. Excepteur sint occaecat cupidatat non proident, sunt in culpa qui officia deserunt mollit anim id est laborum Sed ut perspiciatis unde omnis iste natus error sit voluptatem accusantium doloremque laudantium, totam rem aperiam, eaque ipsa quae ab illo inventore veritatis et quasi architecto beatae vitae dicta sunt explicabo. Nemo enim ipsam voluptatem quia voluptas sit aspernatur aut odit aut fugit, sed quia consequuntur magni dolores eos qui ratione voluptatem sequi nesciunt. Neque porro quisquam est, qui dolorem ipsum quia dolor sit amet, consectetur, adipisci velit, sed quia non numquam eius modi tempora incidunt ut labore et dolore magnam aliquam quaerat voluptatem. Ut enim ad minima veniam, quis nostrum exercitationem ullam corporis suscipit laboriosam, nisi ut aliquid ex ea commodi consequatur.</p>
  </div>

  <div class="sec-title h" style="top:1043px">Our Product</div>
  <div class="rule" style="top:1070px"></div>
  <article class="product" style="left:69px;top:1086px"><div class="ph" role="img" aria-label="White two-station restroom trailer" style="background:linear-gradient(#e6e8ea,#c9cdd1)"></div><div class="pt h">2 Station Luxury Restroom Trailer</div><p>Lorem ipsum dolor sit amet, consectetur adip iscing elit, sed do eiusmod tempor.</p><div class="btn-line">ADD FOR QUOTE</div></article>
  <article class="product" style="left:238px;top:1086px"><div class="ph" role="img" aria-label="Restroom trailer at a construction site" style="background:linear-gradient(#8fb6dc,#a8794e)"></div><div class="pt h">5 Station Luxury Restroom Trailer</div><p>Lorem ipsum dolor sit amet, consectetur adip iscing elit, sed do eiusmod tempor.</p><div class="btn-line">ADD FOR QUOTE</div></article>
  <article class="product" style="left:406px;top:1086px"><div class="ph" role="img" aria-label="Large restroom trailer with people outside" style="background:linear-gradient(135deg,#b9b4aa,#5a5048)"></div><div class="pt h">9 Station Luxury Restroom Trailer</div><p>Lorem ipsum dolor sit amet, consectetur adip iscing elit, sed do eiusmod tempor.</p><div class="btn-line">ADD FOR QUOTE</div></article>
  <article class="product" style="left:69px;top:1283px"><div class="ph" role="img" aria-label="Colourful cleaning supplies" style="background:linear-gradient(135deg,#7a8590,#d85a3a 50%,#4a6ad0)"></div><div class="pt h">Grand Specialty Amenities Package</div><p>Lorem ipsum dolor sit amet, consectetur adip iscing elit, sed do eiusmod tempor.</p><div class="btn-line">ADD FOR QUOTE</div></article>
  <article class="product" style="left:238px;top:1283px"><div class="ph" role="img" aria-label="Hand under a sanitizer dispenser" style="background:linear-gradient(135deg,#e8e6e2,#b98a6c)"></div><div class="pt h">Hand Sanitizer Station Rentals</div><p>Lorem ipsum dolor sit amet, consectetur adip iscing elit, sed do eiusmod tempor.</p><div class="btn-line">ADD FOR QUOTE</div></article>
  <article class="product" style="left:406px;top:1283px"><div class="ph" role="img" aria-label="Restroom attendant cleaning a washroom" style="background:linear-gradient(135deg,#3a4250,#e4e7ea)"></div><div class="pt h">Restroom Attendant</div><p>Lorem ipsum dolor sit amet, consectetur adip iscing elit, sed do eiusmod tempor.</p><div class="btn-line">ADD FOR QUOTE</div></article>

  <footer class="site-footer">
    <div class="contact-row"><span><svg width="6" height="8" viewBox="0 0 12 16"><path fill="#fff" d="M6 0a6 6 0 00-6 6c0 4.5 6 10 6 10s6-5.5 6-10a6 6 0 00-6-6zm0 8.5A2.5 2.5 0 116 3.5a2.5 2.5 0 010 5z"/></svg>123 Lorem ipsum dolor sit amet consectetur</span><span><svg width="7" height="7" viewBox="0 0 24 24"><path fill="#fff" d="M6.6 10.8a15 15 0 006.6 6.6l2.2-2.2a1 1 0 011-.25 11.4 11.4 0 003.6.57 1 1 0 011 1V20a1 1 0 01-1 1A17 17 0 013 4a1 1 0 011-1h3.5a1 1 0 011 1c0 1.25.2 2.45.57 3.57a1 1 0 01-.25 1z"/></svg>+1 555 0142 736</span><span><svg width="8" height="6" viewBox="0 0 16 12"><rect width="16" height="12" rx="1" fill="#fff"/><path d="M1 1l7 5 7-5" fill="none" stroke="#1b2532" stroke-width="1.4"/></svg>hello@tidewellcomforts.com</span></div>
    <div class="foot-nav"><span>HOME</span><span>|</span><span>EVENTS</span><span>|</span><span>PRODUCTS</span><span>|</span><span>CONTACT</span></div>
    <div class="foot-rule"></div>
    <div class="socials"><i></i><i></i><i></i><i></i></div>
    <div class="copy">© Copyrights 2022 Tidewell Comforts &nbsp;|&nbsp; All Rights Reserved</div>
  </footer>

  <div class="dim"></div>

  <form class="quote-modal">
    <div class="h">Contact us for a quote</div>
    <div class="field f-l" style="top:48px"><b><i></i></b>Full Name</div>
    <div class="field f-r" style="top:48px"><b><i></i></b>Phone Number</div>
    <div class="field f-w" style="top:80px"><b><i></i></b>Email Address</div>
    <div class="field f-l" style="top:112px"><b><i></i></b>Type Of Event ?<em></em></div>
    <div class="field f-r" style="top:112px"><b><i></i></b>How Many People ?<em></em></div>
    <div class="field f-w" style="top:143px"><b><i></i></b>Type Of Product You're Interested In ?<em></em></div>
    <div class="field f-l" style="top:175px"><b><i></i></b>Where Do You Need It ?<em></em></div>
    <div class="field f-r" style="top:175px"><b><i></i></b>For How Long ?<em></em></div>
    <div class="field f-w" style="top:206px"><b><i></i></b>Where ?</div>
    <div class="btn-submit">SUBMIT</div>
  </form>
  <div class="wheel" style="left:95px;top:505px;width:144px;height:144px" role="img" aria-label="Photo of a trailer tyre"><span></span></div>
  <div class="wheel" style="left:392px;top:505px;width:144px;height:144px" role="img" aria-label="Photo of a trailer tyre"><span></span></div>
</section>

</div>
</body>
</html>
```